Maple Roster Business Card for recruitment company

We are looking for a Business Card Design that incorporates our personal details and our busines name and logo. We are a specialized search consultancy that recruit Property and Construction professionals.
We would like a business card that stands out and is appealing to the Construction and Property industry as well.

Target Market(s)

people in the construction and property industry

Contact Information for Business Card

Business Name and logo

Font styles to use
Serif

Colors
0094D4
00A9DD
6FCCEA
C7EBF8
E9F6FB

Requirements
Must have
• Business name and logo as well as contact details
Should not have
• No photos of us please

```html
<!DOCTYPE html>
<html lang="en">
<head>
<meta charset="utf-8">
<title>Maple Roster Business Card</title>
<link rel="stylesheet" href="https://fonts.googleapis.com/css2?family=Open+Sans:wght@300;400;700&display=swap">
<style>
  :root {
    --stage: #24272b;
    --card: #003d55;
    --band: #e9ecee;
    --band-text: #4a5560;
    --ink: #ffffff;
    --rule: #a3adb3;
  }
  * { margin: 0; padding: 0; box-sizing: border-box; }
  html, body { width: 1200px; height: 780px; overflow: hidden; }
  body {
    background: var(--stage);
    font-family: "Open Sans", sans-serif;
    position: relative;
  }
  .card {
    position: absolute;
    top: 241px;
    width: 520px;
    height: 298px;
    background: var(--card);
    border-radius: 16px;
    overflow: hidden;
    color: var(--ink);
  }
  .card--details { left: 45px; }
  .card--brand { left: 635px; }

  .wordmark {
    position: absolute;
    font-weight: 300;
    text-transform: uppercase;
    color: var(--ink);
    white-space: nowrap;
  }
  .card--details .wordmark {
    left: 30px; top: 54px;
    font-size: 27px;
    letter-spacing: 1px;
  }
  .card--brand .wordmark {
    left: 0; right: 0; top: 98px;
    text-align: center;
    font-size: 50px;
    letter-spacing: 2px;
  }

  .divider {
    position: absolute;
    left: 236px; top: 96px;
    width: 1px; height: 176px;
    background: var(--rule);
  }
  .person {
    position: absolute;
    left: 254px; top: 96px;
    right: 0;
  }
  .person__name {
    font-size: 22px;
    font-weight: 700;
    letter-spacing: 0.8px;
    line-height: 1.1;
  }
  .person__role {
    font-size: 12px;
    letter-spacing: 0.5px;
    margin-top: 2px;
    padding-bottom: 6px;
    border-bottom: 1px solid var(--rule);
  }
  .contacts {
    list-style: none;
    position: absolute;
    left: 254px; top: 160px;
    font-size: 13.5px;
    letter-spacing: 0.6px;
    line-height: 1.35;
  }
  .contacts li {
    display: flex;
    align-items: flex-start;
    gap: 10px;
    margin-bottom: 5px;
  }
  .contacts svg {
    flex: none;
    width: 14px; height: 14px;
    margin-top: 2px;
    fill: none;
    stroke: var(--ink);
    stroke-width: 1.4;
  }

  .band {
    position: absolute;
    left: 0; right: 0; bottom: 0;
    height: 38px;
    background: var(--band);
    display: flex;
    align-items: center;
    gap: 8px;
    padding-left: 26px;
    color: var(--band-text);
    font-size: 14px;
    font-weight: 700;
    letter-spacing: 1.4px;
  }
  .band svg {
    width: 15px; height: 15px;
    fill: none;
    stroke: var(--band-text);
    stroke-width: 1.4;
  }
</style>
</head>
<body>

<section class="card card--details" aria-label="Card back with contact details">
  <div class="wordmark">Maple Roster</div>
  <div class="divider"></div>
  <div class="person">
    <div class="person__name">Idris Kaleem</div>
    <div class="person__role">General Manager</div>
  </div>
  <ul class="contacts">
    <li>
      <svg viewBox="0 0 16 16" aria-hidden="true"><path d="M3 2l3 0 1 3.5-2 1.2a8 8 0 0 0 4.3 4.3l1.2-2 3.5 1v3a1.5 1.5 0 0 1-1.6 1.5A12 12 0 0 1 1.5 3.6 1.5 1.5 0 0 1 3 2z"/></svg>
      <span>041-572-3908</span>
    </li>
    <li>
      <svg viewBox="0 0 16 16" aria-hidden="true"><rect x="1.5" y="3.5" width="13" height="9"/><path d="M1.5 3.5l6.5 5.5 6.5-5.5"/></svg>
      <span>hello@mapleroster.com</span>
    </li>
    <li>
      <svg viewBox="0 0 16 16" aria-hidden="true"><circle cx="8" cy="8" r="6.5"/><ellipse cx="8" cy="8" rx="3" ry="6.5"/><path d="M1.5 8h13M2.5 4.8h11M2.5 11.2h11"/></svg>
      <span>www.mapleroster.com</span>
    </li>
    <li>
      <svg viewBox="0 0 16 16" aria-hidden="true"><path d="M8 14.5s4.5-4.6 4.5-8a4.5 4.5 0 0 0-9 0c0 3.4 4.5 8 4.5 8z"/><circle cx="8" cy="6.5" r="1.6"/></svg>
      <span>4720 Birchwood Lane<br>Dalton, OR 97410</span>
    </li>
  </ul>
</section>

<section class="card card--brand" aria-label="Card front with company name">
  <div class="wordmark">Maple Roster</div>
  <div class="band">
    <svg viewBox="0 0 16 16" aria-hidden="true"><circle cx="8" cy="8" r="6.5"/><ellipse cx="8" cy="8" rx="3" ry="6.5"/><path d="M1.5 8h13M2.5 4.8h11M2.5 11.2h11"/></svg>
    <span>www.mapleroster.com</span>
  </div>
</section>

</body>
</html>
```